CalmPeak Nurses' Manifesto

Design a manifesto to inspire and motivate nurses to work at minimum standards of excellence in their nursing practice.

The manifesto will become a feature of our website, at conferences, workshops and retreats. It will also be featured on other marketing tools.

Primary Market:
Nurses and/or other healthcare professionals (specifically Doctors, Occupational Therapists, Psychologists and Social Workers).

However the manifesto is equally applicable to all nurses and healthcare professionals from new graduates to very experienced senior clinicians, administration officers,managers and healthcare executive personnel.

Mainly females and primarily 35 to 65 years old, which suggests people in this target age group have extensive experience, but have become jaded'.

The purpose of our business is to assist healthcare professionals, primarily nurses, to maintain their enthusiasm and excellence in service provision, for their benefit as well as the benefit of the clients.

I have attached:
File 1: Copy Samples and examples: which has the copy for the manifesto, examples that appeal to us and our 3 attempts.
File 2: Our colour Spec Sheet, HOWEVER the colours are not necessary limited to these colours. These colours are not in the logo that will be on the manifesto. The colours on the logo attached can/or also be used.
File 3: Prototype logo. The final logo will be available within 3 to 4 days.

Industry/Entity Type

Healthcare

Requirements
Must have
• Must use the copy as per the attached file.

It should be contemporary, eye catching and motivational.

Should not have
• MUST BE EASY TO READ. Each line MUST be clearly defined from each other.

```html
<!DOCTYPE html>
<html lang="en">
<head>
<meta charset="utf-8">
<title>CalmPeak – A Nurses' Manifesto</title>
<link rel="stylesheet" href="https://fonts.googleapis.com/css2?family=Cinzel:wght@600;700&family=Open+Sans:wght@300;400;600&display=swap">
<style>
  :root {
    --teal: #5ec5c7;
    --white: #ffffff;
    --orange: #ef5a2a;
    --ink: #2b2b2b;
    --serif: "Cinzel", serif;
    --sans: "Open Sans", sans-serif;
  }
  * { margin: 0; padding: 0; box-sizing: border-box; }
  html, body { width: 848px; height: 1200px; overflow: hidden; background: var(--teal); }
  .manifesto { position: relative; width: 848px; height: 1200px; background: var(--teal); color: var(--white); overflow: hidden; }
  .line { position: absolute; white-space: nowrap; line-height: 1; }
  .serif { font-family: var(--serif); font-weight: 700; }
  .sans { font-family: var(--sans); font-weight: 400; }
  .thin { font-family: var(--sans); font-weight: 300; }

  .brand-panel {
    position: absolute; left: 445px; top: 0; width: 355px; height: 188px;
    background: var(--white); border-radius: 0 0 22px 22px;
    color: var(--ink); font-family: var(--sans); text-align: center;
  }
  .brand-name { position: absolute; top: 62px; width: 100%; font-size: 38px; font-weight: 600; }
  .brand-tag { position: absolute; top: 150px; width: 100%; font-size: 22px; font-weight: 400; }

  .callout {
    position: absolute; background: var(--white); color: var(--orange);
    font-family: var(--serif); font-weight: 700; border-radius: 10px; white-space: nowrap;
  }
  .callout-care { left: 400px; top: 335px; width: 410px; height: 80px; font-size: 40px; line-height: 36px; padding: 6px 0 0 26px; letter-spacing: 4px; }
  .callout-band { left: 38px; top: 560px; width: 762px; height: 52px; font-size: 44px; line-height: 54px; text-align: center; letter-spacing: 4px; }
  .callout-dream { left: 38px; top: 1142px; width: 762px; height: 58px; font-size: 56px; line-height: 62px; text-align: center; letter-spacing: 10px; border-radius: 10px 10px 0 0; }

  .icon { position: absolute; }
</style>
</head>
<body>
<main class="manifesto">

  <div class="line thin" style="left:36px;top:28px;font-size:96px;">NURSE</div>
  <div class="line sans" style="left:40px;top:136px;font-size:26px;">WITH OPEN <span style="font-size:40px;">HANDS,</span></div>
  <div class="line sans" style="left:38px;top:182px;font-size:44px;">HEARTS &amp; MINDS</div>

  <div class="brand-panel">
    <div class="brand-name">CalmPeak</div>
    <div class="brand-tag">A Nurses' Manifesto</div>
  </div>

  <div class="line serif" style="left:40px;top:246px;font-size:17px;line-height:21px;letter-spacing:1px;">DELIGHT YOUR CLIENTS<br>&amp; COLLEAGUES BY<br>EXCEEDING THEIR</div>
  <svg class="icon" style="left:228px;top:274px;" width="60" height="34" viewBox="0 0 60 34" aria-label="Nurse cap">
    <path d="M4 6 Q30 -2 56 6 L52 30 Q30 26 8 30 Z" fill="var(--white)"/>
    <rect x="27" y="8" width="6" height="18" fill="var(--orange)"/>
    <rect x="21" y="14" width="18" height="6" fill="var(--orange)"/>
  </svg>

  <div class="line serif" style="left:310px;top:228px;font-size:20px;letter-spacing:4px;">LOOK AFTER <span style="font-size:40px;letter-spacing:3px;">YOURSELF</span> &amp;</div>
  <div class="line serif" style="left:310px;top:272px;font-size:22px;letter-spacing:3.3px;">VALUE YOUR HEALTH AS MUCH AS</div>
  <div class="line serif" style="left:310px;top:297px;font-size:21px;letter-spacing:2.8px;">YOU VALUE THE HEALTH OF OTHERS.</div>

  <div class="line serif" style="left:38px;top:334px;font-size:40px;letter-spacing:3px;">EXPECTATIONS</div>
  <div class="callout callout-care">DELIVER CARE<br>SKILLFULLY.</div>

  <div class="line serif" style="left:38px;top:384px;font-size:36px;letter-spacing:4px;">RESPECT <span style="font-size:14px;letter-spacing:1.3px;">THE LIMITS OF</span></div>
  <div class="line serif" style="left:38px;top:417px;font-size:14px;line-height:16px;letter-spacing:1.6px;">PEOPLE'S KNOWLEDGE &amp; SHARE YOUR<br>KNOWLEDGE GENEROUSLY.</div>

  <div class="line sans" style="left:38px;top:465px;font-size:36px;line-height:42px;letter-spacing:1px;">LEARN SOMETHING<br>NEW EACH DAY.</div>

  <div class="line serif" style="left:400px;top:445px;font-size:19px;letter-spacing:1px;"><span style="font-size:36px;">SUPPORT</span> YOUR COLLEAGUES</div>
  <div class="line serif" style="left:400px;top:480px;font-size:19px;letter-spacing:1px;">&amp; CHAMPION THEIR <span style="font-size:36px;">PURPOSE.</span></div>
  <div class="line serif" style="left:400px;top:514px;font-size:12.5px;line-height:15px;letter-spacing:1.7px;">TRUST YOUR KNOWLEDGE &amp; SEEK ADVICE<br>ONLY FROM RESPECTED SOURCES.</div>

  <div class="callout callout-band">BE A LIFELONG LEARNER.</div>

  <div class="line serif" style="left:38px;top:636px;font-size:46px;line-height:38px;letter-spacing:4px;">CELEBRATE,<br>RESPECT &amp;<br>VALUE</div>
  <svg class="icon" style="left:262px;top:712px;" width="88" height="78" viewBox="0 0 76 68" aria-label="Heart with heartbeat line">
    <path d="M38 66 L6 34 A18 18 0 0 1 38 10 A18 18 0 0 1 70 34 Z" fill="var(--white)"/>
    <polyline points="10,36 26,36 31,26 37,48 43,18 48,40 52,36 66,36" fill="none" stroke="var(--orange)" stroke-width="3" stroke-linejoin="round"/>
  </svg>

  <div class="line serif" style="left:392px;top:634px;font-size:26px;line-height:28px;letter-spacing:5.5px;">THE DIVERSITY OF<br>AUSTRALIAN CULTURE.</div>
  <div class="line serif" style="left:392px;top:700px;font-size:38px;letter-spacing:2px;">SMILE</div>
  <div class="line serif" style="left:548px;top:702px;font-size:15px;letter-spacing:3.2px;">&amp; INFECT OTHERS WITH</div>
  <div class="line serif" style="left:684px;top:719px;font-size:13px;letter-spacing:1px;">YOUR</div>
  <div class="line serif" style="left:392px;top:738px;font-size:22px;letter-spacing:5.5px;">HAPPINESS &amp; HAVE FUN!</div>

  <div class="line serif" style="left:38px;top:768px;font-size:15px;line-height:18px;letter-spacing:3px;">YOU ARE UNIQUE,<br>REVEL IN YOUR</div>
  <div class="line serif" style="left:38px;top:802px;font-size:39px;">INDIVIDUALITY.</div>

  <div class="line serif" style="left:386px;top:778px;font-size:19px;letter-spacing:4.5px;">ALWAYS DO THE</div>
  <div class="line serif" style="left:618px;top:774px;font-size:46px;letter-spacing:4px;">RIGHT</div>
  <div class="line serif" style="left:386px;top:798px;font-size:48px;letter-spacing:6px;">THING</div>
  <div class="line serif" style="left:596px;top:823px;font-size:15px;letter-spacing:2px;">WITHOUT EXCEPTION.</div>

  <div class="line serif" style="left:38px;top:860px;font-size:36px;letter-spacing:4px;">SEEK SUCCESS</div>
  <div class="line serif" style="left:38px;top:900px;font-size:36px;letter-spacing:1.5px;">FIRSTLY FROM WITHIN.</div>
  <div class="line sans" style="left:386px;top:866px;font-size:26px;letter-spacing:0.6px;">ALWAYS BE SOLUTION FOCUSED.</div>
  <div class="line serif" style="left:548px;top:908px;font-size:16px;line-height:16px;letter-spacing:4.5px;">ALWAYS LEAD WITH<br>PURPOSE, PASSION<br>&amp; COMMITMENT.</div>

  <div class="line serif" style="left:38px;top:954px;font-size:21px;letter-spacing:2px;">ONLY FOLLOW EXCEPTIONAL LEADERS.</div>
  <div class="line serif" style="left:38px;top:986px;font-size:21px;letter-spacing:2.6px;">IF THERE IS NO ONE LEFT TO FOLLOW, THEN LEAD!</div>

  <div class="line serif" style="left:38px;top:1022px;font-size:12.5px;line-height:15px;letter-spacing:2.2px;">RESPOND TO COMPLEX SITUATIONS INNOVATIVELY,<br>CREATIVELY &amp; SAFELY WITHIN THE SCOPE OF</div>
  <div class="line serif" style="left:480px;top:1016px;font-size:33px;letter-spacing:2.5px;">YOUR PRACTICE.</div>

  <div class="line serif" style="left:38px;top:1074px;font-size:14px;letter-spacing:3px;">ADOPT A <span style="font-size:24px;letter-spacing:2px;">'CAN DO'</span></div>
  <div class="line serif" style="left:38px;top:1098px;font-size:14px;line-height:16px;letter-spacing:3.5px;">ATTITUDE TO EVERYTHING<br>THAT COMES YOUR WAY.</div>
  <div class="line sans" style="left:330px;top:1064px;font-size:23px;letter-spacing:1.3px;">CHOOSE YOUR THOUGHTS WISELY,</div>
  <div class="line sans" style="left:330px;top:1094px;font-size:23px;letter-spacing:0.6px;">THEY <span style="font-size:28px;">CREATE YOUR REALITY.</span></div>

  <div class="callout callout-dream">LIVE YOUR DREAM.</div>

</main>
</body>
</html>
```